Flowy subpage design wanted for a modern tax/accounting firm in Switzerland

--- Introduction ---
We are a tax and accounting firm in Switzerland. We provide services for expats living in Switzerland, our service is quite exclusive and modern (digital).

We just relaunched our website www.fiscavantra.ch and are happy with the design, so the desired subpage (more details below) should of course fit in.

--- Main brief ---
Please see Word File attached. The page has to include the whole text (11 chapters). A very intuitive, flowy design on only one subpage (not one page per chapter) is a MUST. Also, it is key that the design is supporting the content of the individual chapters, so it would be advantageous if you'd have a good unterstanding of the text attached.

--- Further information ---
A similar example would be this one: https://www2.brennick.com/ch/en/pages/tax/articles/living-working-switzerland.html

This one is similar in what concerns the content, but NOT what we are looking for designwise. It is very simple and looks "thrown together", just not aesthetically pleasing in our opinion.

--- Final thoughts ---
- If you blow our minds with your design, we will certainly have future work for you.
- Our clients are between 20-50 years old, well educated, high income / high wealth, English speaking and living in Switzerland.
- CI/CD information:
Fonts
Montserrat regular / medium italic / bold
Colors
White #ffffffff
Darkblue #0a2b46
Darkblue 25% #b5bfc8
Darkblue 50% #8595a4
Greenblue #0d4261

We are looking forward to your designs!
Updates

Thank you very much for the submitted designs and your efforts. Unfortunately, none of the designs meet our expectations so far. Please note the following: - Designs that do not take CI into account will not be looked at more closely. - We have received many simple designs with very simple structure and accordion elements. But more important than the simple structure is an eye-catching design! Make it flowy and beautiful - We don't want pictures of Swiss vehicles, passes or other pictures that don't actively support the text. If you can make an illustration that really fits the context, fine, otherwise better leave it without. Thank you

Target Market(s)

Expats living in Switzerland. High income earners / high net worth individuals

Industry/Entity Type

tax/accounting

Number of Pages Required

1 page

Font styles to use
Other font styles liked:
• Montserrat

Colors
0054AA
0677BA
7BADD7
CADEEF
E8F1F8

Requirements
Must have
• based on general website design
Nice to have
• intuitive, flowy, attractive representation of much text
Should not have
• basic copy/paste of the text in sections :)

```html
<!DOCTYPE html>
<html lang="en">
<head>
<meta charset="utf-8">
<title>Living and working in Switzerland – Fiscavantra Advisory</title>
<link href="https://fonts.googleapis.com/css2?family=Montserrat:wght@300;400;500;600;700&display=swap" rel="stylesheet">
<style>
:root{
  --dark:#0a2b46;
  --greenblue:#0d4261;
  --teal:#063246;
  --blue25:#b5bfc8;
  --blue50:#8595a4;
  --hero:#eef0f3;
  --soft:#f8f9fa;
  --acc:#e2e7ea;
  --white:#ffffff;
}
*{margin:0;padding:0;box-sizing:border-box}
html,body{width:871px;height:1200px;overflow:hidden;background:var(--white)}
body{font-family:'Montserrat',sans-serif;color:var(--dark);position:relative}
.abs{position:absolute}
.hero-shapes{position:absolute;left:0;top:0}
.brand{position:absolute;display:flex;align-items:center;gap:6px}
.brand-dot{width:28px;height:28px;border-radius:50%;border:2px solid var(--dark)}
.brand-name{font-weight:500;font-size:11px;line-height:12px;letter-spacing:.5px;color:var(--dark)}
.brand-footer .brand-dot{border-color:var(--white);width:38px;height:38px}
.brand-footer .brand-name{color:var(--white);font-size:14px;line-height:16px}
.nav a{position:absolute;top:16px;font-size:7px;color:var(--blue50);text-decoration:none;white-space:nowrap}
.btn-calc{position:absolute;left:774px;top:13px;width:65px;height:19px;background:var(--dark);color:var(--white);font-size:7px;display:flex;align-items:center;gap:6px;padding-left:8px}
.btn-calc i{width:7px;height:9px;border:1px solid var(--white);display:block}
.eyebrow{left:154px;top:118px;font-size:11px;color:var(--greenblue)}
.hero-title{left:154px;top:136px;font-size:28px;line-height:34px;color:var(--greenblue);font-weight:400}
.hero-title b{font-weight:700}
.chapters{left:154px;top:335px;width:563px;display:grid;grid-template-columns:repeat(3,1fr);border:1px solid var(--blue50);border-right:none;border-bottom:none}
.chapters div{height:27px;display:flex;align-items:center;justify-content:center;font-size:10px;color:var(--blue50);border-right:1px solid var(--blue50);border-bottom:1px solid var(--blue50);white-space:nowrap}
.chapters .active{background:var(--greenblue);color:var(--white)}
.chapter-num{left:410px;top:462px;font-size:72px;font-weight:700;color:#f3f4f6}
.chapter-title{left:0;width:871px;top:483px;text-align:center;font-size:27px;line-height:28px;color:var(--greenblue);font-weight:400}
.chapter-title b{font-weight:700;display:block}
.intro{left:174px;width:540px;top:546px;text-align:center;font-size:7px;line-height:13.5px;color:var(--greenblue)}
.soft-band{left:0;top:620px;width:871px;height:375px;background:var(--soft)}
.tabs a{position:absolute;top:604px;font-size:9px;color:var(--greenblue);text-decoration:none;white-space:nowrap}
.tabs .current{font-weight:600;border-bottom:2px solid var(--greenblue);padding:0 12px 4px}
.acc{left:154px;top:637px;width:563px}
.acc-head{height:23px;background:var(--greenblue);color:var(--white);font-size:8.5px;display:flex;align-items:center;padding-left:18px;gap:20px}
.acc-head i{width:10px;height:1px;background:var(--white);display:block}
.acc-body{background:var(--white);padding:7px 28px 6px 18px;font-size:7px;line-height:13.6px;color:var(--blue50);font-weight:300}
.acc-list{background:var(--acc)}
.acc-list div{height:22.5px;display:flex;align-items:center;padding-left:18px;gap:20px;font-size:8.5px;color:var(--greenblue)}
.acc-list svg{width:11px;height:11px}
.footer{left:0;top:995px;width:871px;height:205px;background:linear-gradient(90deg,#0c2a45,#1a4168)}
.f-contact{position:absolute;left:157px;font-size:6.5px;font-weight:500;color:var(--white);display:flex;align-items:center;gap:5px}
.f-contact svg{width:8px;height:8px}
.f-head{position:absolute;top:1047px;font-size:8.5px;font-weight:700;color:var(--white);letter-spacing:-.3px}
.f-rule{position:absolute;top:1063px;width:18px;height:1.5px;background:var(--white)}
.f-about{left:346px;top:1079px;width:180px;font-size:6.5px;line-height:13.7px;color:var(--blue25)}
.f-links{left:584px;top:1078px;font-size:6.5px;line-height:15.7px;color:var(--white)}
.f-line{left:0;top:1177px;width:871px;height:1px;background:rgba(255,255,255,.25)}
.f-copy{left:0;width:871px;top:1186px;text-align:center;font-size:6.5px;color:var(--blue25)}
</style>
</head>
<body>

<svg class="hero-shapes" width="871" height="400" viewBox="0 0 871 400">
  <defs>
    <linearGradient id="bldg" x1="0" y1="0" x2="1" y2="1">
      <stop offset="0" stop-color="#e9e4dc"/>
      <stop offset=".5" stop-color="#b9b3aa"/>
      <stop offset="1" stop-color="#6f7478"/>
    </linearGradient>
  </defs>
  <polygon points="0,0 871,0 871,230 560,251 0,286" fill="var(--hero)"/>
  <polygon points="560,251 871,230 871,350" fill="var(--teal)"/>
  <polygon role="img" aria-label="Photo of a modern office building facade seen from below" points="478,234 583,35 871,45 871,230 560,251" fill="url(#bldg)"/>
</svg>

<header>
  <div class="brand" style="left:154px;top:5px">
    <span class="brand-dot"></span>
    <span class="brand-name">FISCAVANTRA<br>ADVISORY</span>
  </div>
  <nav class="nav">
    <a style="left:402px">Home</a>
    <a style="left:440px">Tax returns</a>
    <a style="left:496px">More services ▾</a>
    <a style="left:559px">Swiss tax guide</a>
    <a style="left:629px">About us</a>
  </nav>
  <div class="btn-calc"><i></i>Calculate</div>
</header>

<p class="abs eyebrow">About Switzerland</p>
<h1 class="abs hero-title"><b>Living and working</b><br>in Switzerland</h1>

<div class="abs chapters">
  <div class="active">Life in Switzerland</div>
  <div>Brief Overview of alpine country</div>
  <div>Immigrating to Switzerland</div>
  <div>labor law in Switzerland</div>
  <div>Switzerland double tax agreements</div>
  <div>Indirect taxes in Switzerland</div>
  <div>Federal taxes in Switzerland</div>
  <div>Rent and buy in Switzerland</div>
  <div>Childcare in Switzerland</div>
  <div>Public transportation in Switzerland</div>
  <div>Recreation</div>
  <div></div>
</div>

<span class="abs chapter-num">1</span>
<h2 class="abs chapter-title"><b>Life in</b>Switzerland</h2>
<p class="abs intro">To give you a small impression of what to expect when living in Switzerland, we have put together some topics for you to make your new start in Switzerland as pleasant as possible.</p>

<div class="abs soft-band"></div>
<nav class="tabs">
  <a class="current" style="left:172px">General</a>
  <a style="left:248px">Living in Switzerland</a>
  <a style="left:368px">Education system</a>
  <a style="left:476px">Healthcare system</a>
  <a style="left:587px">Driving</a>
  <a style="left:648px">Public transport</a>
</nav>

<section class="abs acc">
  <div class="acc-head"><i></i>4 official languages</div>
  <div class="acc-body">Unlike many other countries in Europe, where there is usually only one official national language, Switzerland has four of them: German, French, Italian and Romansh. The most widespread language is German, which is spoken mainly in central Switzerland and the cantons bordering Germany. French dominates in the western part of Switzerland, and Italian in the southeastern part. Rhaeto-Romanic is spoken by only a very small part of the total population in eastern Switzerland. In each region, there are also different dialects in the various languages. Official documents are generally issued in German, French and Italian.</div>
  <div class="acc-list">
    <div><svg viewBox="0 0 11 11"><path d="M5.5 0v11M0 5.5h11" stroke="var(--greenblue)"/></svg>Currency and banking</div>
    <div><svg viewBox="0 0 11 11"><path d="M5.5 0v11M0 5.5h11" stroke="var(--greenblue)"/></svg>Public holidays</div>
    <div><svg viewBox="0 0 11 11"><path d="M5.5 0v11M0 5.5h11" stroke="var(--greenblue)"/></svg>Usual business and store opening hours</div>
    <div><svg viewBox="0 0 11 11"><path d="M5.5 0v11M0 5.5h11" stroke="var(--greenblue)"/></svg>Electricity and water</div>
    <div><svg viewBox="0 0 11 11"><path d="M5.5 0v11M0 5.5h11" stroke="var(--greenblue)"/></svg>Telephone and television</div>
  </div>
</section>

<footer class="abs footer"></footer>
<div class="brand brand-footer" style="left:157px;top:1042px">
  <span class="brand-dot"></span>
  <span class="brand-name">FISCAVANTRA<br>ADVISORY</span>
</div>
<div class="f-contact" style="top:1100px"><svg viewBox="0 0 8 8"><path d="M4 0a3 3 0 0 1 3 3c0 2-3 5-3 5S1 5 1 3a3 3 0 0 1 3-3z" fill="#fff"/><circle cx="4" cy="3" r="1" fill="#12385c"/></svg>Office Zug | Lindenweg 14</div>
<div class="f-contact" style="top:1116px"><svg viewBox="0 0 8 8"><path d="M1 1l2 0 1 2-1 1c.5 1 1 1.5 2 2l1-1 2 1v2C4 8 0 4 1 1z" fill="#fff"/></svg>Available for existing clients only</div>
<div class="f-contact" style="top:1132px"><svg viewBox="0 0 8 8"><rect x="0" y="1.5" width="8" height="5" fill="#fff"/><path d="M0 1.5l4 3 4-3" stroke="#12385c" fill="none" stroke-width=".7"/></svg>Available for existing clients only</div>

<h3 class="f-head" style="left:346px">ABOUT FISCAVANTRA</h3>
<span class="f-rule" style="left:346px"></span>
<p class="abs f-about">Fiscavantra Advisory was founded in 2014 with the vision to make Swiss tax matters uncomplicated and painless for expats without compromising quality or making the service unaffordable.</p>

<h3 class="f-head" style="left:584px">QUICK LINKS</h3>
<span class="f-rule" style="left:584px"></span>
<ul class="abs f-links" style="list-style:none">
  <li>Tax returns</li>
  <li>Nordalp AG</li>
  <li>Swiss tax guide</li>
  <li>About us</li>
  <li>Privacy policy</li>
</ul>

<div class="abs f-line"></div>
<p class="abs f-copy">2022 Fiscavantra Advisory LLC All Right Reserved | Privacy Policy | Impressum</p>

</body>
</html>
```